Business Card Design needed for start up company Halvora

In need of a new business card designed for a start up company based in Sydney, Halvora is a new start up innovative Company, our mission it to make property accessible for everyday Australian and to become the leading Real Estate platform in Australia. We want it to be fresh and clean.

Industry/Entity Type

Financial

Contact Information for Business Card

Section for Name
Section for Title

HALVORA - The Strength of Pooling
Mobile:
Direct:

Font styles to use
Sans Serif

Colors
33a6d7
0692cd
0255a3
ffffff

Requirements
Must have
• Logo, all business card details

```html
<!DOCTYPE html>
<html lang="en">
<head>
<meta charset="utf-8">
<title>Halvora Business Card</title>
<link href="https://fonts.googleapis.com/css2?family=Arimo:wght@400;700&family=Montserrat:wght@800&display=swap" rel="stylesheet">
<style>
  :root {
    --stage: #c9c9c9;
    --sky: #33a6d7;
    --ocean: #0692cd;
    --navy: #1d4474;
    --deep: #0255a3;
    --ink: #666666;
    --white: #ffffff;
    --card-front-top: #f7f7f7;
    --card-front-bottom: #d9d9d9;
    --card-back-top: #2299d2;
    --card-back-bottom: #1b78a8;
  }
  html, body {
    margin: 0;
    padding: 0;
    width: 1200px;
    height: 965px;
    overflow: hidden;
    background: var(--stage);
    font-family: "Arimo", Arial, sans-serif;
  }
  .canvas {
    position: relative;
    width: 1200px;
    height: 965px;
  }
  .card {
    position: absolute;
    left: 277px;
    width: 648px;
    height: 368px;
    border-radius: 36px;
    overflow: hidden;
  }
  .card--front {
    top: 97px;
    background: linear-gradient(180deg, var(--card-front-top) 0%, var(--white) 40%, var(--card-front-bottom) 100%);
  }
  .card--back {
    top: 502px;
    background: linear-gradient(180deg, var(--card-back-top) 0%, var(--card-back-bottom) 100%);
  }
  .logo {
    position: absolute;
    display: block;
  }
  .card--front .logo {
    left: 59px;
    top: 136px;
  }
  .card--back .logo {
    left: 90px;
    top: 114px;
  }
  .divider {
    position: absolute;
    left: 404px;
    top: 60px;
    width: 2px;
    height: 256px;
    background: linear-gradient(180deg, rgba(29,68,116,0) 0%, var(--navy) 20%, var(--navy) 80%, rgba(29,68,116,0) 100%);
  }
  .details {
    position: absolute;
    left: 432px;
    top: 78px;
  }
  .person-name {
    margin: 0;
    font-size: 20px;
    font-weight: 700;
    color: var(--ocean);
    line-height: 22px;
  }
  .person-title {
    margin: 0;
    font-size: 14px;
    color: var(--navy);
    line-height: 18px;
  }
  .contact-list {
    list-style: none;
    margin: 34px 0 0;
    padding: 0;
  }
  .contact-item {
    display: flex;
    align-items: center;
    height: 19px;
    font-size: 14.5px;
    color: var(--ink);
  }
  .contact-icon {
    width: 14px;
    height: 14px;
    margin: 0 10px 0 2px;
    flex: none;
  }
  .address {
    margin: 26px 0 0;
    font-size: 14.5px;
    line-height: 19px;
    color: var(--ink);
  }
</style>
</head>
<body>
<div class="canvas">

  <section class="card card--front" aria-label="Card front">
    <svg class="logo" width="340" height="100" viewBox="0 0 340 100" aria-label="Halvora">
      <circle cx="49" cy="49" r="49" fill="var(--ocean)"/>
      <text x="108" y="71" font-family="Montserrat, sans-serif" font-weight="800" font-size="44" fill="var(--navy)" textLength="214" lengthAdjust="spacingAndGlyphs">HALVORA</text>
    </svg>

    <div class="divider"></div>

    <div class="details">
      <p class="person-name">Marcus Ellery</p>
      <p class="person-title">Managing Director</p>
      <ul class="contact-list">
        <li class="contact-item">
          <svg class="contact-icon" viewBox="0 0 14 14"><rect x="1" y="2" width="3" height="11" rx="1" fill="var(--ocean)"/><rect x="5" y="3" width="8" height="10" rx="1" fill="none" stroke="var(--ocean)" stroke-width="1.5"/><rect x="7" y="5" width="4" height="2" fill="var(--ocean)"/></svg>
          +61 2 9471 5580
        </li>
        <li class="contact-item">
          <svg class="contact-icon" viewBox="0 0 14 14"><path d="M3 1 L5.5 4 L4 6 Q5.5 9 8 10 L10 8.5 L13 11 L11 13 Q6 13 3 9.5 Q0.5 6 1 3 Z" fill="var(--ocean)"/></svg>
          +61 412 308 276
        </li>
        <li class="contact-item">
          <svg class="contact-icon" viewBox="0 0 14 14"><rect x="1" y="3" width="12" height="9" fill="none" stroke="var(--ocean)" stroke-width="1.5"/><path d="M1 3 L7 8 L13 3 M1 12 L5.5 7 M13 12 L8.5 7" fill="none" stroke="var(--ocean)" stroke-width="1.3"/></svg>
          info@halvora.com
        </li>
        <li class="contact-item">
          <svg class="contact-icon" viewBox="0 0 14 14"><g fill="none" stroke="var(--ocean)" stroke-width="1.1"><circle cx="7" cy="7" r="6"/><ellipse cx="7" cy="7" rx="2.6" ry="6"/><path d="M1 7 H13 M2 4 H12 M2 10 H12"/></g></svg>
          www.halvora.com
        </li>
      </ul>
      <p class="address">Here your company or<br>home address</p>
    </div>
  </section>

  <section class="card card--back" aria-label="Card back">
    <svg class="logo" width="480" height="146" viewBox="0 0 480 146" aria-label="Halvora">
      <circle cx="71" cy="71" r="71" fill="var(--white)"/>
      <text x="145" y="112" font-family="Montserrat, sans-serif" font-weight="800" font-size="66" fill="var(--white)" textLength="322" lengthAdjust="spacingAndGlyphs">HALVORA</text>
    </svg>
  </section>

</div>
</body>
</html>
```